New Innovative Counselling and psychotherapy Service needs Business Card design

Keep it simple and professional. On one side, just company name and logo (perhaps in all blue) and maybe a tag line.

On other side (all white) my name and Qualifications in centre

Industry/Entity Type

Health And Wellness

Contact Information for Business Card

Dara Whelby
Counsellor & Psychotherapist
BSc (Psychol.), BA, Dip. (Couns. & Psych.), PG.Cert (CBT), FGTrK, ONRE

I will also require Mobile no, Email and web site address of which I'll pass on to final designer.

Font styles to use
Sans Serif

Requirements
Must have
• My Logo Only and please use the colours in logo that is in it.
Should not have
• Any other images

```html
<!DOCTYPE html>
<html lang="en">
<head>
<meta charset="utf-8">
<title>Harbor Lane – Business Card</title>
<link rel="stylesheet" href="https://fonts.googleapis.com/css2?family=Open+Sans:wght@300;400;600;700&display=swap">
<style>
  :root {
    --bg: #e9ecef;
    --card-white: #ffffff;
    --brand-blue: #4ab3ea;
    --brand-green: #8dd15a;
    --ink: #3a3a3a;
    --ink-soft: #6b6b6b;
    --on-blue: #ffffff;
  }
  * { box-sizing: border-box; margin: 0; padding: 0; }
  html, body {
    width: 1200px; height: 900px; overflow: hidden;
    background: var(--bg);
    font-family: "Open Sans", sans-serif;
  }
  .canvas {
    position: relative; width: 1200px; height: 900px;
    display: flex; flex-direction: column; align-items: center; justify-content: center; gap: 36px;
  }
  .card {
    position: relative; width: 700px; height: 400px;
    box-shadow: 0 10px 30px rgba(0,0,0,0.15);
    overflow: hidden;
  }
  /* Front */
  .card-front { background: var(--card-white); }
  .brand {
    position: absolute; left: 0; right: 0; top: 145px;
    display: flex; align-items: center; justify-content: center; gap: 22px;
  }
  .brand-dot {
    width: 64px; height: 64px; border-radius: 50%;
    background: var(--brand-blue);
  }
  .brand-name {
    font-size: 46px; font-weight: 300; color: var(--ink); letter-spacing: 0.5px;
  }
  .tagline {
    position: absolute; left: 0; right: 0; bottom: 58px;
    text-align: center; font-size: 17px; color: var(--ink-soft); letter-spacing: 0.3px;
  }
  /* Back */
  .card-back { background: var(--brand-blue); color: var(--on-blue); }
  .back-brand {
    position: absolute; right: 40px; top: 70px;
    display: flex; flex-direction: column; align-items: center; gap: 22px;
  }
  .back-brand-dot {
    width: 170px; height: 170px; border-radius: 50%;
    background: var(--on-blue);
  }
  .back-brand-name { font-size: 30px; font-weight: 300; color: var(--on-blue); }
  .person { position: absolute; left: 42px; top: 112px; }
  .person-name { font-size: 24px; font-weight: 700; text-transform: uppercase; letter-spacing: 0.5px; }
  .person-role { font-size: 17px; font-weight: 400; text-transform: uppercase; margin-top: 2px; }
  .person-quals { font-size: 14px; font-weight: 400; line-height: 1.35; margin-top: 6px; max-width: 330px; }
  .contact { position: absolute; left: 42px; bottom: 36px; list-style: none; }
  .contact li { display: flex; align-items: center; gap: 12px; font-size: 18px; line-height: 1.5; }
  .contact svg { width: 18px; height: 18px; flex: none; }
</style>
</head>
<body>
<main class="canvas">
  <section class="card card-front" aria-label="Card front">
    <div class="brand">
      <span class="brand-dot"></span>
      <span class="brand-name">Harbor Lane</span>
    </div>
    <p class="tagline">Caring For Your Psychological Well-Being Is Our Top Priority</p>
  </section>

  <section class="card card-back" aria-label="Card back">
    <div class="back-brand">
      <span class="back-brand-dot"></span>
      <span class="back-brand-name">Harbor Lane</span>
    </div>
    <div class="person">
      <h1 class="person-name">Dara Whelby</h1>
      <p class="person-role">Counsellor &amp; Psychotherapist</p>
      <p class="person-quals">BSc (Psychol.), BA, Dip. (Couns. &amp; Psych.), PG.Cert. (CBT), FGTrK,</p>
    </div>
    <ul class="contact">
      <li>
        <svg viewBox="0 0 18 18" aria-hidden="true"><rect x="4" y="1" width="10" height="16" rx="2" fill="none" stroke="#fff" stroke-width="1.8"/><circle cx="9" cy="14" r="1" fill="#fff"/></svg>
        555 210 4817
      </li>
      <li>
        <svg viewBox="0 0 18 18" aria-hidden="true"><rect x="1" y="4" width="16" height="11" fill="#fff"/><path d="M1 4 L9 10 L17 4" fill="none" stroke="#4ab3ea" stroke-width="1.5"/></svg>
        dara@Harborlane.com
      </li>
      <li>
        <svg viewBox="0 0 18 18" aria-hidden="true"><circle cx="9" cy="9" r="7.5" fill="none" stroke="#fff" stroke-width="1.6"/><ellipse cx="9" cy="9" rx="3.2" ry="7.5" fill="none" stroke="#fff" stroke-width="1.3"/><line x1="1.5" y1="9" x2="16.5" y2="9" stroke="#fff" stroke-width="1.3"/></svg>
        www.Harborlane.com
      </li>
    </ul>
  </section>
</main>
</body>
</html>
```